Birch And Harbor Website A Website design for book editing

A website design for book editing

Our proofreading, editing and manuscript review packages are specifically tailored to help you publish the best possible version of your story.

NEED HELP PUBLISHING A BESTSELLER?

If you’re looking for professional book editing services from senior publishing industry insiders, look no further. Besides editing, we can also answer all your publishing questions and get you started building your author platform.

OUR SERVICES

We've carefully structured our packages to maximize value for every budget.

PRICING

$.02
PER WORD
Proofreading
Line Edit (Copy-editing)
Fix spelling and grammar
Sales copy/summary revision

$.04
PER WORD
Proofreading
Line Edit (Copy-editing)
Fix spelling and grammar
Organization and content
Plot and pacing
Manuscript Review

$.06
PER WORD
Proofreading
Line Edit (Copy-editing)
Fix spelling and grammar
Organization and content
Plot and pacing
Manuscript Review
Formatting (print and ebook)
Pre-publication proofread

OUR PROCESS

Send us a sample of your book. Our caffeine-fueled, eagle-eyed editors will go through it and then email you with their comments and suggestions. You can ask them any questions you want. They will look for…

Typos and grammatical errors.
Spelling and word choice issues
Punctuation and style
Word choice, clarity and flow.
Sentence structure and craft
If your writing is already clean, then they’ll discuss bigger picture things with you, like theme, concept, purpose, audience, potential market and branding (including title, subtitle, and tagline or elevator pitch).

Once you feel comfortable and confident in an editor’s expertise, skill and knowledge, and are ready to move ahead, we’ll send an invoice for the first half of the total word count so the editor can get started. We’ll charge the rest when the project is close to completion.

Target Market(s)

Authors

Industry/Entity Type

Book Publisher

Coding

Coded - Design and coding required

Number of Pages Required

1 page

Requirements
Must have
• OUR SERVICES
• We've carefully structured our packages to maximize value for every budget.
• PRICING
• $.02
• PER WORD
• Proofreading
• Line Edit (Copy-editing)
• Fix spelling and grammar
• Sales copy/summary revision
• $.04
• PER WORD
• Proofreading
• Organization and content
• Plot and pacing
• Manuscript Review
• $.06
• PER WORD
• Proofreading
• Plot and pacing
• Manuscript Review
• Formatting (print and ebook)
• Pre-publication proofread

```html
<!DOCTYPE html>
<html lang="en">
<head>
<meta charset="utf-8">
<title>Birch And Harbor – Book Editing</title>
<link href="https://fonts.googleapis.com/css2?family=Poppins:wght@400;500;600;700&display=swap" rel="stylesheet">
<style>
:root{
  --red:#e5101d;
  --ink:#141414;
  --text:#333333;
  --grey-band:#767676;
  --light:#ececec;
  --footer:#f1f1f1;
  --white:#ffffff;
  --placeholder-a:#f3f3f3;
  --placeholder-b:#dedede;
}
*{box-sizing:border-box;margin:0;padding:0}
html,body{width:1200px;height:3719px;overflow:hidden}
body{font-family:'Poppins',sans-serif;color:var(--text);background:var(--white);position:relative}
.abs{position:absolute}

/* header */
.site-header{position:absolute;top:0;left:0;width:1200px;height:104px;background:var(--white);z-index:2}
.brand{position:absolute;left:134px;top:36px;display:flex;align-items:center;gap:9px;font-size:23px;font-weight:700;color:var(--red);white-space:nowrap}
.brand-dot{width:20px;height:20px;border-radius:50%;background:var(--red)}
.main-nav span{position:absolute;top:46px;font-size:14px;font-weight:500;color:var(--ink);white-space:nowrap}
.btn-pill{display:inline-block;background:var(--red);color:var(--white);border-radius:30px;font-weight:600;text-transform:uppercase;text-align:center;white-space:nowrap}
.nav-cta{position:absolute;left:932px;top:39px;width:134px;height:34px;line-height:34px;font-size:13px}

/* hero */
.hero{position:absolute;top:104px;left:0;width:1200px;height:603px}
.hero-photo{position:absolute;inset:0;background:linear-gradient(90deg,#f4f5f6 0%,#eef0f2 38%,#d8dde3 55%,#c9d3de 70%,#e9ecef 100%)}
.hero-title{position:absolute;left:134px;top:120px;font-size:36px;line-height:60px;font-weight:700;color:var(--ink)}
.hero-title em{font-style:normal;color:var(--red)}
.hero-text{position:absolute;left:134px;top:246px;width:420px;font-size:13px;line-height:23px;color:var(--text)}
.hero-cta{position:absolute;left:134px;top:340px;width:275px;height:36px;line-height:36px;font-size:13px}
.slider-dots{position:absolute;left:134px;top:415px;display:flex;gap:8px;align-items:center}
.slider-dots i{width:11px;height:11px;border-radius:50%;background:#333}
.slider-dots i.on{width:17px;height:17px;border:2px solid var(--red);background:radial-gradient(var(--red) 40%,#fff 45%)}

/* services */
.services{position:absolute;top:711px;left:0;width:1200px;height:449px;background:linear-gradient(135deg,#d90b18,var(--red) 50%,#ef1d2a)}
.section-title-light{position:absolute;top:54px;width:100%;text-align:center;color:var(--white);font-size:28px;font-weight:600}
.service{position:absolute;top:144px;width:220px;text-align:center;color:var(--white)}
.service-icon{width:104px;height:104px;margin:0 auto;border:3px solid var(--white);border-radius:50%;display:flex;align-items:center;justify-content:center}
.service h3{margin-top:28px;font-size:13px;line-height:21px;font-weight:600;text-transform:uppercase}
.service p{margin-top:12px;font-size:11.5px;line-height:19px;opacity:.92}

/* welcome */
.welcome{position:absolute;top:1160px;left:0;width:1200px;height:546px;background:var(--white)}
.welcome-title{position:absolute;left:131px;top:122px;color:var(--ink);font-size:33px;line-height:47px;font-weight:500}
.welcome-title strong{display:block;font-weight:700;font-size:37px}
.welcome-text{position:absolute;left:131px;top:236px;width:480px;font-size:12.5px;line-height:25px}
.btn-outline{position:absolute;left:131px;top:383px;width:130px;height:35px;line-height:31px;border:2px solid var(--ink);border-radius:30px;text-align:center;font-size:13px;font-weight:600;color:var(--ink)}
.video-frame{position:absolute;left:662px;top:112px;width:429px;height:315px}
.video-photo{position:absolute;left:8px;top:8px;right:8px;bottom:8px;background:linear-gradient(120deg,#8a98a6,#c9b46a 40%,#5d7e9e 70%,#3a4654)}
.play{position:absolute;left:50%;top:50%;width:62px;height:62px;margin:-31px 0 0 -31px;border-radius:50%;background:var(--white);display:flex;align-items:center;justify-content:center}

/* pricing */
.pricing{position:absolute;top:1706px;left:0;width:1200px;height:778px;background:var(--light)}
.section-title{position:absolute;width:100%;text-align:center;font-size:37px;font-weight:700;color:var(--ink)}
.section-title em{font-style:normal;color:var(--red)}
.plan{position:absolute;background:var(--white);box-shadow:0 4px 18px rgba(0,0,0,.12);text-align:center}
.plan-name{height:59px;line-height:59px;font-size:24px;font-weight:600;color:var(--ink)}
.plan-price{height:80px;background:var(--grey-band);color:var(--white);display:flex;align-items:center;justify-content:center}
.plan-price b{font-size:44px;font-weight:600;line-height:1}
.plan-price sup{font-size:22px;font-weight:500;align-self:flex-start;margin-top:14px;margin-right:4px}
.plan-price small{font-size:13px;margin-left:2px;margin-top:10px}
.plan ul{list-style:none;padding-top:14px}
.plan li{font-size:12.5px;line-height:32px;border-bottom:1px solid #eeeeee;margin:0 20px;color:var(--text)}
.plan li:last-child{border-bottom:none}
.plan-standard{left:178px;top:193px;width:268px;height:461px}
.plan-pro{left:751px;top:193px;width:268px;height:461px}
.plan-premium{left:446px;top:171px;width:305px;height:503px;background:#121212;z-index:1}
.plan-premium .plan-name{height:67px;line-height:67px;color:var(--white);font-size:25px}
.plan-premium .plan-price{background:var(--red)}
.plan-premium li{color:var(--white);border-bottom-color:#2b2b2b}
.plan-cta{margin-top:18px;width:100px;height:30px;line-height:30px;font-size:11px;border-radius:3px}

/* process */
.process{position:absolute;top:2484px;left:0;width:1200px;height:545px}
.process-intro{position:absolute;left:200px;top:150px;width:800px;text-align:center;font-size:12.5px;line-height:25px}
.steps{position:absolute;left:0;top:252px;width:1200px;height:200px}
.step{position:absolute;top:0;width:200px;text-align:center}
.step-art{width:150px;height:118px;margin:0 auto;border-radius:59px;background:linear-gradient(135deg,var(--placeholder-a),var(--placeholder-b))}
.step p{margin-top:22px;font-size:15px;line-height:24px;color:var(--ink)}

/* newsletter */
.newsletter{position:absolute;top:3029px;left:0;width:1200px;height:441px;background:linear-gradient(180deg,#161616,#0c0c0c);clip-path:polygon(0 70px,50% 0,100% 70px,100% 100%,0 100%)}
.newsletter h2{position:absolute;top:184px;width:100%;text-align:center;color:var(--white);font-size:35px;font-weight:600}
.newsletter p{position:absolute;top:250px;width:100%;text-align:center;color:var(--white);font-size:17px}
.subscribe{position:absolute;left:335px;top:307px;width:538px;height:42px;background:var(--white);border-radius:30px}
.subscribe span{position:absolute;left:22px;top:0;line-height:42px;font-size:12px;color:#666}
.subscribe .btn-pill{position:absolute;right:0;top:0;width:155px;height:42px;line-height:42px;font-size:15px}

/* footer */
.site-footer{position:absolute;top:3470px;left:0;width:1200px;height:249px;background:var(--footer);text-align:center;color:var(--ink)}
.social{position:absolute;top:45px;left:0;width:100%;display:flex;justify-content:center;gap:8px}
.social i{width:30px;height:30px;border-radius:50%;border:2px solid var(--ink)}
.footer-phone{position:absolute;top:96px;width:100%;font-size:14px}
.footer-links{position:absolute;top:131px;width:100%;font-size:14px}
.footer-links span{margin:0 8px}
.footer-copy{position:absolute;top:166px;width:100%;font-size:14px}
</style>
</head>
<body>

<header class="site-header">
  <div class="brand"><span class="brand-dot"></span>Birch And Harbor</div>
  <nav class="main-nav">
    <span style="left:414px">HOME</span>
    <span style="left:486px">OUR SERVICES</span>
    <span style="left:615px">PRICING</span>
    <span style="left:704px">ABOUT US</span>
    <span style="left:806px">OUR PROCESS</span>
  </nav>
  <a class="btn-pill nav-cta">Get Started</a>
</header>

<section class="hero">
  <div class="hero-photo" role="img" aria-label="Writer with glasses working at a laptop on a bright desk with notes and pencils"></div>
  <h1 class="hero-title">NEED HELP <em>PUBLISHING</em><br>A BESTSELLER?</h1>
  <p class="hero-text">Sed ut perspiciatis unde omnis iste natus error sit voluptatem accusantium doloremque laudantium, totam rem aperiam, eaque ipsa quae ab illo inventore veritatis</p>
  <a class="btn-pill hero-cta">View Pricing and Order Now</a>
  <div class="slider-dots"><i class="on"></i><i></i><i></i><i></i></div>
</section>

<section class="services">
  <h2 class="section-title-light">OUR SERVICES</h2>
  <div class="service" style="left:118px">
    <div class="service-icon"><svg width="48" height="48" viewBox="0 0 48 48" fill="none" stroke="#fff" stroke-width="3" stroke-linejoin="round"><rect x="6" y="10" width="30" height="32" rx="5"/><path d="M20 30l2-7 18-18 5 5-18 18z"/></svg></div>
    <h3>Professional Editing<br>Feedback, Proofreading</h3>
    <p>Sed ut perspiciatis unde omnis iste natus error sit voluptatem accusantium doloremque laudium</p>
  </div>
  <div class="service" style="left:366px">
    <div class="service-icon"><svg width="48" height="48" viewBox="0 0 48 48" fill="none" stroke="#fff" stroke-width="3" stroke-linejoin="round"><path d="M12 6h26v32H14a4 4 0 0 0 0 8h24"/><path d="M12 6a4 4 0 0 0-4 4v30"/><path d="M18 16h14M18 23h14"/></svg></div>
    <h3>Your Book is in<br>Expert Hands</h3>
    <p>Sed ut perspiciatis unde omnis iste natus error sit voluptatem accusantium doloremque laudium</p>
  </div>
  <div class="service" style="left:614px">
    <div class="service-icon"><svg width="48" height="48" viewBox="0 0 48 48" fill="none" stroke="#fff" stroke-width="3" stroke-linecap="round"><circle cx="24" cy="24" r="18"/><path d="M24 13v12h8"/></svg></div>
    <h3>Affordable and Always<br>Available to You</h3>
    <p>Sed ut perspiciatis unde omnis iste natus error sit voluptatem accusantium doloremque laudium</p>
  </div>
  <div class="service" style="left:862px">
    <div class="service-icon"><svg width="48" height="48" viewBox="0 0 48 48"><path d="M24 4l17 6v12c0 11-7 19-17 22C14 41 7 33 7 22V10z" fill="#fff"/><path d="M24 9v30c-7-3-12-9-12-17v-8z" fill="var(--red)"/></svg></div>
    <h3>Completely<br>Confidential &amp; Secure</h3>
    <p>Sed ut perspiciatis unde omnis iste natus error sit voluptatem accusantium doloremque laudium</p>
  </div>
</section>

<section class="welcome">
  <h2 class="welcome-title">WELCOME TO<strong>BIRCH AND HARBOR</strong></h2>
  <p class="welcome-text">Sed ut perspiciatis unde omnis iste natus error sit voluptatem accusantium doloremque laudantium, totam rem aperiam, eaque ipsa quae ab illo inventore veritatis et quasi architecto beatae vitae dicta sunt explicabo. Nemo enim ipsam voluptatem quia voluptas sit aspernatur aut odit aut fugit, sed quia nior magni dolores eos qui ratione voluptatem</p>
  <a class="btn-outline">READ MORE</a>
  <div class="video-frame">
    <svg class="abs" style="left:0;top:0" width="429" height="315" fill="none" stroke="#333" stroke-width="2"><path d="M1 30V1h30M398 1h30v29M428 285v29h-30M31 314H1v-29"/></svg>
    <div class="video-photo" role="img" aria-label="Two colleagues reviewing work together at a computer in an office"></div>
    <div class="play"><svg width="24" height="24" viewBox="0 0 24 24"><path d="M7 4l14 8-14 8z" fill="#222"/></svg></div>
  </div>
</section>

<section class="pricing">
  <h2 class="section-title" style="top:66px"><em>OUR</em> PRICING</h2>
  <div class="plan plan-standard">
    <div class="plan-name">Standard</div>
    <div class="plan-price"><sup>$</sup><b>.02</b><small>PER WORD</small></div>
    <ul><li>Proofreading</li><li>Line Edit (Copy-editing)</li><li>Fix spelling and grammar</li><li>Sales copy/summary revision</li></ul>
  </div>
  <div class="plan plan-premium">
    <div class="plan-name">Premium</div>
    <div class="plan-price"><sup>$</sup><b>.04</b><small>PER WORD</small></div>
    <ul><li>Proofreading</li><li>Line Edit (Copy-editing)</li><li>Fix spelling and grammar</li><li>Sales copy/summary revision</li><li>Organization and content</li><li>Plot and pacing</li><li>Manuscript Review</li></ul>
    <a class="btn-pill plan-cta">Get Started</a>
  </div>
  <div class="plan plan-pro">
    <div class="plan-name">Professional</div>
    <div class="plan-price"><sup>$</sup><b>.06</b><small>PER WORD</small></div>
    <ul><li>Proofreading</li><li>Line Edit (Copy-editing)</li><li>Fix spelling and grammar</li><li>Sales copy/summary revision</li><li>Organization and content</li><li>Plot and pacing</li><li>Manuscript Review</li><li>Formatting (print and ebook)</li><li>Pre-publication proofread</li></ul>
  </div>
</section>

<section class="process">
  <h2 class="section-title" style="top:90px"><em>OUR</em> PROCESS</h2>
  <p class="process-intro">Sed ut perspiciatis unde omnis iste natus error sit voluptatem accusantium doloremque laudantium, totam rem aperiam, eaque ipsa quae ab illo inventore veritatis et quasi architecto beatae vitae dicta sunt explicabo.</p>
  <div class="steps">
    <svg class="abs" style="left:0;top:0" width="1200" height="120"><path d="M230 59H980" stroke="#999" stroke-width="2" stroke-dasharray="3 6"/></svg>
    <div class="step" style="left:98px">
      <div class="step-art" role="img" aria-label="Step 1 illustration: outlined numeral one with a checklist icon"></div>
      <p>Typos and<br>grammatical errors.</p>
    </div>
    <div class="step" style="left:297px">
      <div class="step-art" role="img" aria-label="Step 2 illustration: outlined numeral two with a magnifier icon"></div>
      <p>Spelling and word<br>choice issues</p>
    </div>
    <div class="step" style="left:496px">
      <div class="step-art" role="img" aria-label="Step 3 illustration: outlined numeral three with an alert icon"></div>
      <p>Punctuation and<br>style</p>
    </div>
    <div class="step" style="left:695px">
      <div class="step-art" role="img" aria-label="Step 4 illustration: outlined numeral four with a target icon"></div>
      <p>Word choice, clarity<br>and flow.</p>
    </div>
    <div class="step" style="left:894px">
      <div class="step-art" role="img" aria-label="Step 5 illustration: outlined numeral five with a text icon"></div>
      <p>Sentence structure<br>and craft</p>
    </div>
  </div>
</section>

<section class="newsletter">
  <h2>JOIN OUR NEWSLETTER</h2>
  <p>Professional Editing And Proofreading To Prepare Your Book For Publishing</p>
  <div class="subscribe"><span>Enter Your Email</span><a class="btn-pill">Get Started</a></div>
</section>

<footer class="site-footer">
  <div class="social"><i></i><i></i><i></i></div>
  <p class="footer-phone">Toll Free: 320-555-0186</p>
  <p class="footer-links"><span>Request Quote</span>|<span>Contact Us</span>|<span>Site Map</span>|<span>FAQ</span>|<span>My Account</span></p>
  <p class="footer-copy">Copyright 2018 Birch And Harbor, All rights reserved.</p>
</footer>

</body>
</html>
```